Dental specialist needs a sharp looking letterhead

I am looking for a letterhead to be used to send letters and communication between myself (a dental specialist) and other dentists.
My office is a state of the art dental specialty office.
I need to letterhead to also state:
Bertram L. Oswick DDS
2748 Tollard Avenue, Suite K
West Tollard, NY 14391
(716)392-5061
fax: (716)392-5087
oswickroot.com (**this email address may change)

i included my logo designs.
thank you

Target Market(s)

dentists

Industry/Entity Type

Communication

Requirements
Must have
• the included logo, whether the vertical or horizontal versions

```html
<!DOCTYPE html>
<html lang="en">
<head>
<meta charset="utf-8">
<title>Tollard Endodontics Letterhead</title>
<link href="https://fonts.googleapis.com/css2?family=Roboto+Slab:wght@400;500&display=swap" rel="stylesheet">
<style>
  :root {
    --backdrop: #ebebec;
    --paper: #ffffff;
    --band: #0b0b0b;
    --blue: #3d9fdc;
    --green: #8cc63f;
    --white: #ffffff;
  }
  * { margin: 0; padding: 0; box-sizing: border-box; }
  html, body {
    width: 1200px;
    height: 942px;
    overflow: hidden;
    background: var(--backdrop);
    font-family: "Roboto Slab", Georgia, serif;
  }
  .letterhead {
    position: absolute;
    left: 268px;
    top: 41px;
    width: 665px;
    height: 860px;
    background: var(--paper);
    box-shadow: 0 6px 20px rgba(0,0,0,0.12);
    display: flex;
  }
  .sidebar {
    width: 196px;
    height: 100%;
    background: var(--band);
    border-right: 3px solid var(--blue);
    box-shadow: 3px 0 0 var(--green);
    display: flex;
    flex-direction: column;
    justify-content: space-between;
    padding: 40px 18px 30px 20px;
  }
  .brand {
    display: flex;
    align-items: center;
    gap: 10px;
    margin-bottom: 22px;
  }
  .brand-mark {
    width: 34px;
    height: 34px;
    border-radius: 50%;
    background: var(--blue);
    flex-shrink: 0;
  }
  .brand-name {
    color: var(--white);
    font-weight: 500;
    font-size: 13px;
    line-height: 1.25;
    letter-spacing: 0.04em;
    text-transform: uppercase;
  }
  .doctor-name {
    color: var(--white);
    font-size: 13px;
    font-weight: 400;
    margin-bottom: 10px;
  }
  .contact-list { list-style: none; }
  .contact-list li {
    display: flex;
    align-items: flex-start;
    gap: 7px;
    color: var(--blue);
    font-size: 10.5px;
    line-height: 1.35;
    margin-bottom: 5px;
  }
  .icon {
    width: 11px;
    height: 11px;
    flex-shrink: 0;
    margin-top: 2px;
  }
  .web-list { list-style: none; }
  .web-list li {
    display: flex;
    align-items: center;
    gap: 7px;
    color: var(--green);
    font-size: 10.5px;
    margin-top: 6px;
  }
  .writing-area { flex: 1; }
</style>
</head>
<body>
  <div class="letterhead">
    <aside class="sidebar">
      <div class="sidebar-top">
        <div class="brand">
          <span class="brand-mark"></span>
          <span class="brand-name">Tollard<br>Endodontics P.C.</span>
        </div>
        <p class="doctor-name">Bertram L. Oswick DDS</p>
        <ul class="contact-list">
          <li>
            <svg class="icon" viewBox="0 0 12 12"><circle cx="6" cy="6" r="6" fill="var(--blue)"/><path d="M4 3.2l1.2 1.3-.6.8a4 4 0 0 0 2 2l.8-.6 1.3 1.2-.7 1A5 5 0 0 1 3 4z" fill="#0b0b0b"/></svg>
            <span>(716)392-5061</span>
          </li>
          <li>
            <svg class="icon" viewBox="0 0 12 12"><circle cx="6" cy="6" r="6" fill="var(--blue)"/><rect x="3" y="4.5" width="6" height="3.5" fill="#0b0b0b"/><rect x="4" y="3" width="4" height="1.5" fill="#0b0b0b"/></svg>
            <span>(716)392-5087</span>
          </li>
          <li>
            <svg class="icon" viewBox="0 0 12 12"><circle cx="6" cy="6" r="6" fill="var(--blue)"/><path d="M6 2.5a2.3 2.3 0 0 1 2.3 2.3C8.3 6.5 6 9.5 6 9.5S3.7 6.5 3.7 4.8A2.3 2.3 0 0 1 6 2.5z" fill="#0b0b0b"/><circle cx="6" cy="4.8" r=".8" fill="var(--blue)"/></svg>
            <span>2748 Tollard Avenue, Suite K<br>West Tollard, NY 14391</span>
          </li>
        </ul>
      </div>
      <ul class="web-list">
        <li>
          <svg class="icon" viewBox="0 0 12 12"><circle cx="6" cy="6" r="6" fill="var(--green)"/><rect x="2.8" y="3.8" width="6.4" height="4.4" fill="#0b0b0b"/><path d="M2.8 3.8L6 6.3l3.2-2.5" stroke="var(--green)" stroke-width=".8" fill="none"/></svg>
          <span>bertram@oswickroot.com</span>
        </li>
        <li>
          <svg class="icon" viewBox="0 0 12 12"><circle cx="6" cy="6" r="6" fill="var(--green)"/><circle cx="6" cy="6" r="3.4" fill="none" stroke="#0b0b0b" stroke-width=".9"/><path d="M2.6 6h6.8M6 2.6c-1.6 2-1.6 4.8 0 6.8M6 2.6c1.6 2 1.6 4.8 0 6.8" stroke="#0b0b0b" stroke-width=".8" fill="none"/></svg>
          <span>www.oswickroot.com</span>
        </li>
      </ul>
    </aside>
    <main class="writing-area"></main>
  </div>
</body>
</html>
```